We want to revamp our current website -www.kelvota-eng.com

We need to have a new website for our company that offers non-destructive and testing solutions around Africa. We have a current website but it does not fulfil our needs as it is:<br/>1. Not clear and bright<br/>2. Does not fit well in mobile <br/>3. Is not easily updatable by our staff. <br/>4. Is not linked to our social media sites.<br/>We would like to have a website that addresses the above issues. Our colours are Red and Blue and should communicate to our clients, that we are a professional company open for business, ready to solve their non-destructive testing problems around Africa. * Helpful if it is a wordpress website.

Target Market(s)

Our customers are B2B Corporate clients. We mainly work in
1. Storage Terminals
2. Refineries
3. Oil and Gas offshore and onshore rigs.

Industry/Entity Type

Oil And Gas

Contact Information for Business Card

Please find our current business card on the uploaded files.

Coding

Coded - Design and coding required

Number of Pages Required

5+ page

Font styles to use
Serif
Sans Serif

Requirements
Must have
• I like this site www.pirelo-inspection.com They are in the same industry.
• I don't understand how to call them but all the 'call to action' buttons, and links to our Social media pages.
• Must have a place where we update information in a regular basis. A Blog!

```html
<!DOCTYPE html>
<html lang="en">
<head>
<meta charset="utf-8">
<title>Kelvota Engineering</title>
<link href="https://fonts.googleapis.com/css2?family=Signika:wght@400;500;600&family=Roboto:wght@400;500;700&display=swap" rel="stylesheet">
<style>
:root{
  --blue:#273b7b;
  --blue-dark:#1d2d62;
  --red:#b71c23;
  --red-dark:#8f1016;
  --grey:#f2f2f2;
  --text:#444;
  --white:#fff;
}
*{margin:0;padding:0;box-sizing:border-box}
html,body{width:1200px;height:4992px;overflow:hidden}
body{position:relative;font-family:"Roboto",sans-serif;color:var(--text);background:var(--white)}
.abs{position:absolute}
h1,h2,h3,h4{font-family:"Signika",sans-serif;font-weight:500}
.btn{display:inline-block;border:2px solid var(--white);outline:2px solid var(--red);background:var(--red);color:var(--white);font-family:"Signika",sans-serif;text-transform:uppercase;border-radius:30px;text-align:center}
.red{color:var(--red)}
.sec-title{font-size:40px;color:var(--blue);text-align:center;text-transform:uppercase;letter-spacing:.5px}

/* header */
.header{top:0;left:0;width:1200px;height:151px}
.brand{left:100px;top:14px;display:flex;align-items:center;gap:14px}
.brand-dot{width:64px;height:64px;border-radius:50%;background:var(--red)}
.brand-name{font-family:"Signika",sans-serif;font-size:27px;font-weight:500;color:var(--blue);text-transform:uppercase}
.tagline{left:530px;top:26px;width:330px;font-size:13px;line-height:20px;text-align:center;color:var(--blue);text-transform:uppercase;border-left:2px solid #bbb;border-right:2px solid #bbb;padding:0 20px}
.cta-top{left:912px;top:26px;width:196px;height:42px;line-height:38px;font-size:18px}
.nav{top:107px;left:90px;width:1015px;height:44px;background:var(--blue);clip-path:polygon(0 0,100% 0,98.5% 100%,1.5% 100%)}
.nav ul{list-style:none;display:flex;gap:22px;padding:16px 0 0 28px}
.nav li{color:var(--white);font-size:15px;text-transform:uppercase}
.nav li.active{border-bottom:2px solid var(--white);padding-bottom:4px}
.nav-rule{top:150px;left:0;width:1200px;height:3px;background:var(--blue)}

/* hero */
.hero{top:153px;left:0;width:1200px;height:587px;background:radial-gradient(ellipse at 30% 30%,#6b6a6e 0%,#3a3d4a 40%,#1c2233 100%)}
.hero-title{top:372px;left:0;width:1200px;text-align:center;color:var(--white);font-size:54px;text-transform:uppercase;letter-spacing:1px}
.hero-cta{top:460px;left:490px;width:220px;height:48px;line-height:44px;font-size:21px}

/* welcome */
.welcome{top:830px;left:0;width:1200px}
.welcome p{width:900px;margin:30px auto 0;text-align:center;font-size:16.5px;line-height:33px}

/* split */
.split{top:1040px;left:0;width:1200px;height:445px}
.split svg{position:absolute;top:0;left:0}
.panel{position:absolute;top:110px;width:490px;color:var(--white)}
.panel h3{font-size:31px;text-transform:uppercase;margin-bottom:20px}
.panel p{font-size:15.5px;line-height:32.5px;text-align:justify}
.panel.left{left:90px;top:112px}
.panel.right{left:626px;top:104px}

/* industries */
.industries{top:1500px;left:0;width:1200px}
.industries p{width:820px;margin:18px auto 0;text-align:center;font-size:16.5px;line-height:32px}
.track{top:1655px;left:0;width:1200px;height:193px;overflow:hidden}
.card{position:absolute;top:0;width:229px;height:193px;background:linear-gradient(180deg,#5f6a7c 0%,#2e3646 100%)}
.card span{position:absolute;bottom:14px;left:18px;color:var(--white);font-family:"Signika",sans-serif;font-size:17px}
.card.active{background:linear-gradient(180deg,#324a94,var(--blue))}
.card.active h4{color:var(--white);text-align:center;font-size:18px;margin-top:34px}
.card.active p{color:var(--white);font-size:12.5px;line-height:21px;text-align:justify;padding:0 16px;margin-top:6px}
.card .mini{display:block;width:108px;height:22px;line-height:18px;margin:8px auto 0;font-size:9px;border-radius:12px}
.arrow{top:1738px;width:22px;height:30px}

/* about */
.about-media{top:1953px;left:0;width:603px;height:505px;background:linear-gradient(160deg,#6e7a92 0%,#2d3a5a 55%,#c9913f 100%)}
.play{top:2180px;left:274px;width:48px;height:48px;border-radius:50%;background:var(--blue-dark)}
.about{top:1953px;left:603px;width:597px;height:505px;background:var(--grey)}
.about h2{position:absolute;left:50px;top:50px;font-size:40px;color:var(--blue);text-transform:uppercase}
.about p{position:absolute;left:50px;top:118px;width:460px;font-size:15.5px;line-height:32.2px;text-align:justify}
.about .btn{position:absolute;left:50px;top:420px;width:154px;height:34px;line-height:30px;font-size:14px}

/* blog */
.blog-title{top:2550px;left:0;width:1200px}
.post{position:absolute;background:var(--blue);color:var(--white);overflow:hidden}
.post .ph{width:100%}
.post h4{font-size:22px;text-transform:uppercase;margin:12px 10px 6px}
.post .meta{font-size:13px;margin:0 10px 8px;display:flex;gap:18px}
.post .meta i{display:inline-block;width:11px;height:11px;background:var(--white);margin-right:6px;vertical-align:-1px}
.post .meta b{font-weight:400}
.post p{font-size:13px;line-height:21px;margin:0 10px}
.post .more{font-size:13px;font-weight:500;margin:10px 10px 0;text-transform:uppercase}
.post .more::after{content:" \2192";margin-left:10px}
.view-more{top:3416px;left:511px;width:176px;height:40px;line-height:36px;font-size:18px}

/* clients */
.clients{top:3564px;left:0;width:1200px;height:559px;background:var(--red)}
.clients h2{color:var(--white);text-align:center;font-size:40px;text-transform:uppercase;margin-top:48px}
.client{position:absolute;width:231px;height:151px;background:var(--white);border-radius:4px;display:flex;align-items:center;justify-content:center;font-family:"Signika",sans-serif;font-weight:600;font-size:24px;color:var(--blue)}
.dots{position:absolute;top:538px;left:0;width:1200px;display:flex;justify-content:center;gap:12px}
.dots i{width:11px;height:11px;border-radius:50%;background:var(--white)}
.dots i.on{background:#222}

/* map */
.map{top:4231px;left:0;width:1200px;height:425px;background:linear-gradient(135deg,#eef0ea 0%,#e4e6df 60%,#b9d5ea 100%)}
.map-card{top:4360px;left:560px;width:170px;background:var(--white);font-size:12px;line-height:20px;padding:8px 12px;box-shadow:0 2px 6px rgba(0,0,0,.2)}
.pin{top:4465px;left:630px;width:18px;height:18px;border-radius:50% 50% 50% 0;transform:rotate(-45deg);background:var(--red)}

/* footer */
.footer{top:4656px;left:0;width:1200px;height:336px;background:var(--blue);color:var(--white)}
.f-brand{position:absolute;left:90px;top:40px;display:flex;align-items:center;gap:16px}
.f-brand i{width:68px;height:68px;border-radius:50%;background:var(--white)}
.f-brand span{font-family:"Signika",sans-serif;font-size:22px}
.f-about{position:absolute;left:90px;top:128px;width:310px;font-size:14px;line-height:29px;text-align:justify}
.f-col{position:absolute;top:56px}
.f-col h4{font-size:21px;text-transform:uppercase;margin-bottom:14px;line-height:26px}
.f-col li{list-style:none;font-size:14px;line-height:27px}
.f-input{width:196px;height:34px;background:var(--white);color:#333;font-size:11px;padding:10px 6px;margin-top:6px}
.f-send{width:86px;height:18px;line-height:14px;font-size:9px;margin-top:14px;border-width:1px}
.f-bar{position:absolute;left:90px;top:300px;width:1020px;border-top:1px solid rgba(255,255,255,.3);padding-top:12px;font-size:12.5px;display:flex;justify-content:space-between}
.f-social{display:flex;gap:10px}
.f-social i{width:16px;height:16px;background:var(--white)}
</style>
</head>
<body>

<header class="abs header">
  <div class="abs brand"><span class="brand-dot"></span><span class="brand-name">Kelvota Engineering</span></div>
  <div class="abs tagline">Respect and diversity, ethics and integrity, safety and sustainability</div>
  <a class="abs btn cta-top">Get Started</a>
</header>
<nav class="abs nav">
  <ul>
    <li class="active">Home</li><li>About Us</li><li>Inspection NDT Services</li><li>Advanced NDT Services</li><li>Engineering Services</li><li>Blog</li><li>Contact Us</li>
  </ul>
</nav>
<div class="abs nav-rule"></div>

<section class="abs hero" role="img" aria-label="Welder at work with sparks flying in a dark workshop"></section>
<h1 class="abs hero-title">Kelvota Engineering</h1>
<a class="abs btn hero-cta">Get A Quote</a>

<section class="abs welcome">
  <h2 class="sec-title">Welcome to <span class="red">Kelvota Engineering</span></h2>
  <p>With roots in Mombasa, we have over 15 years' experience in NDT, Mechanical engineering and Marine services. We enjoy a regional presence in The larger Eastern and Central African Region. Though our head office is located in Mombasa, Kenya, with a fully fledged testing laboratory not far from our office. We provide testing services across various countries in Africa.</p>
</section>

<section class="abs split">
  <svg width="1200" height="445" viewBox="0 0 1200 445">
    <defs><linearGradient id="gl" x1="0" x2="1"><stop offset="0" stop-color="#000" stop-opacity="0"/><stop offset="1" stop-color="#000" stop-opacity=".5"/></linearGradient></defs>
    <polygon points="0,0 600,75 600,370 0,445" fill="#273b7b"/>
    <polygon points="600,75 1200,0 1200,445 600,370" fill="#b71c23"/>
    <polygon points="0,0 600,75 600,370 0,445" fill="url(#gl)" opacity=".35"/>
  </svg>
  <div class="panel left">
    <h3>Kelvota Inspection Services</h3>
    <p>Lorem ipsum dolor sit amet, consectetur adipiscing elit, sed do eiusmod tempor incididunt ut labore et dolore magna aliqua. Ut enim ad minim veniam, quis nostrud exercitation ullamco laboris nisi ut aliquip ex ea commodo consequat. Duis aute irure dolor in reprehenderit in voluptate velit esse cillum dolore eu fugiat nulla</p>
  </div>
  <div class="panel right">
    <h3>Kelvota Engineering Services.</h3>
    <p>Lorem ipsum dolor sit amet, consectetur adipiscing elit, sed do eiusmod tempor incididunt ut labore et dolore magna aliqua. Ut enim ad minim veniam, quis nostrud exercitation ullamco laboris nisi ut aliquip ex ea commodo consequat. Duis aute irure dolor in reprehenderit in voluptate velit esse cillum dolore eu fugiat nulla</p>
  </div>
</section>

<section class="abs industries">
  <h2 class="sec-title">Industries <span class="red">Served</span></h2>
  <p>Lorem ipsum dolor sit amet, consectetur adipiscing elit, sed do eiusmod tempor incididunt ut labore et dolore magna aliqua. Ut enim ad</p>
</section>
<div class="abs track">
  <div class="card" style="left:-138px" role="img" aria-label="Oil and gas rig at sea"><span>Oil and Gas</span></div>
  <div class="card" style="left:110px" role="img" aria-label="Oil storage tanks by a harbour"><span>Oil Storage and Transport</span></div>
  <div class="card active" style="left:357px">
    <h4>Ports and Harbours</h4>
    <p>Lorem ipsum dolor sit amet, consectetur adipiscing elit, sed do eiusmod tempor</p>
    <span class="btn mini" style="position:static">Read More</span>
  </div>
  <div class="card" style="left:605px;background:linear-gradient(180deg,#8a8fa3,#3b3540)" role="img" aria-label="Pump jack silhouette at sunset"><span style="left:88px">Mining</span></div>
  <div class="card" style="left:852px;background:linear-gradient(180deg,#3d4f70,#1f2a40)" role="img" aria-label="Power station at dusk"><span>Power Generation</span></div>
  <div class="card" style="left:1110px;background:linear-gradient(180deg,#c08040,#5c5a60)" role="img" aria-label="Manufacturing plant"><span>Manufacturing</span></div>
</div>
<svg class="abs arrow" style="left:18px" viewBox="0 0 22 30"><path d="M16 4 6 15l10 11" fill="none" stroke="#fff" stroke-width="3"/></svg>
<svg class="abs arrow" style="left:1152px" viewBox="0 0 22 30"><path d="M6 4l10 11L6 26" fill="none" stroke="#fff" stroke-width="3"/></svg>

<div class="abs about-media" role="img" aria-label="Refinery lit up at night"></div>
<svg class="abs play" viewBox="0 0 48 48"><circle cx="24" cy="24" r="24" fill="#1d2d62"/><circle cx="24" cy="24" r="13" fill="#fff"/><path d="M21 18l8 6-8 6z" fill="#1d2d62"/></svg>
<section class="abs about">
  <h2>About Us</h2>
  <p>We pick the best talent from the industry and have heavily invested in our developing our staff skills further through regular rigorous external and internal training to keep up with the industry trendsWith roots at the Kenyan coast, we have over 10 years' experience in NDT, Mechanical Engineering and Marine Services. We enjoy a presence in the larger East and Central African region. Our head office is located in Mombasa with our workshop at Mazeras, from where we offer our wide array of services.</p>
  <a class="btn">Read More</a>
</section>

<div class="abs blog-title"><h2 class="sec-title">Lastest <span class="red">Blog</span></h2></div>

<article class="post" style="left:90px;top:2652px;width:380px;height:429px">
  <div class="ph" style="height:260px;background:linear-gradient(160deg,#8d9488,#4a5048)" role="img" aria-label="Insulated pipework at an inspection site"></div>
  <h4>Finibus Bonorum</h4>
  <div class="meta"><b><i></i>JAN 31, 2020</b><b><i></i>By Admin / Kelvota Engineering</b></div>
  <p>Lorem ipsum dolor sit amet, consectetur adipiscing elit, sed do eiusmod tempor incididunt ut</p>
  <div class="more">Read More</div>
</article>
<article class="post" style="left:484px;top:2652px;width:304px;height:318px">
  <div class="ph" style="height:188px;background:linear-gradient(180deg,#6f8a5a,#3d4a37)" role="img" aria-label="Team group standing outdoors"></div>
  <h4>Finibus Bonorum</h4>
  <div class="meta"><b><i></i>JAN 21, 2020</b><b><i></i>By Admin / KE</b></div>
  <p>Lorem ipsum dolor sit amet, consectetur</p>
  <div class="more">Read More</div>
</article>
<article class="post" style="left:806px;top:2652px;width:304px;height:318px">
  <div class="ph" style="height:188px;background:linear-gradient(180deg,#a8b4c4,#56687e)" role="img" aria-label="Technicians working on steel structure"></div>
  <h4>Finibus Bonorum</h4>
  <div class="meta"><b><i></i>JAN 11, 2020</b><b><i></i>By Admin / KE</b></div>
  <p>Lorem ipsum dolor sit amet, consectetur</p>
  <div class="more">Read More</div>
</article>
<article class="post" style="left:484px;top:2986px;width:626px;height:376px">
  <div class="ph" style="height:232px;background:linear-gradient(180deg,#4a4f3c,#1a1d1a)" role="img" aria-label="Workers in hi-vis vests inspecting at night"></div>
  <h4>Finibus Bonorum et Malorum</h4>
  <div class="meta"><b><i></i>JAN 19, 2020</b><b><i></i>By Admin / Kelvota Engineering</b></div>
  <p>Lorem ipsum dolor sit amet, consectetur adipiscing elit, sed do eiusmod tempor incididunt ut labore et dolore magna aliqua. laboris nisi ut aliquip ex ea commodo consequat</p>
  <div class="more">Read More</div>
</article>
<article class="post" style="left:90px;top:3096px;width:380px;height:266px">
  <div class="ph" style="height:152px;background:linear-gradient(180deg,#8fa7bf,#4f6377)" role="img" aria-label="Staff in blue shirts posing together"></div>
  <h4 style="margin-top:8px">Finibus Bonorum</h4>
  <div class="meta"><b><i></i>JAN 15, 2020</b><b><i></i>By Admin / Kelvota Engineering</b></div>
  <p>Lorem ipsum dolor sit amet, consectetur adipiscing</p>
  <div class="more" style="margin-top:2px">Read More</div>
</article>
<a class="abs btn view-more">View More</a>

<section class="abs clients">
  <h2>Clients</h2>
  <div class="client" style="left:91px;top:136px">Norvane Oil</div>
  <div class="client" style="left:354px;top:136px">Calder Motors</div>
  <div class="client" style="left:617px;top:136px">Ostrel</div>
  <div class="client" style="left:879px;top:136px">Brandt Halloway</div>
  <div class="client" style="left:91px;top:316px">Petralo</div>
  <div class="client" style="left:354px;top:316px">Tidemark Energy</div>
  <div class="client" style="left:617px;top:316px">Voltera Power</div>
  <div class="client" style="left:879px;top:316px">Marrow Oil</div>
  <div class="dots"><i></i><i class="on"></i><i></i></div>
</section>

<div class="abs map" role="img" aria-label="Street map of central Mombasa showing the office location"></div>
<div class="abs map-card">Harbour Lane, Mombasa<br>+254 20 555 0142/3<br>info@kelvota-eng.com</div>
<div class="abs pin"></div>

<footer class="abs footer">
  <div class="f-brand"><i></i><span>Kelvota Engineering</span></div>
  <p class="f-about">With roots in Mombasa, we have over 15 years experience in NDT, Mechanical engineering and Marine services. We enjoy a regional presence in The larger Eastern and Central African Region.</p>
  <div class="f-col" style="left:452px">
    <h4>Quicks Links</h4>
    <ul><li>Home</li><li>About Us</li><li>Inspection NDT Services</li><li>Advanced NDT Services</li><li>Engineering Services</li><li>Blog</li><li>Contact Us</li></ul>
  </div>
  <div class="f-col" style="left:670px">
    <h4>Services</h4>
    <ul><li>Kelvota Inspection Services</li><li>Kelvota Engineering Services.</li></ul>
  </div>
  <div class="f-col" style="left:914px">
    <h4>Newsletter<br>Subscription</h4>
    <div class="f-input">Enter The Email</div>
    <div class="btn f-send">Send</div>
  </div>
  <div class="f-bar">
    <span>Copyright © 2020 Kelvota Engineering. | Terms of Use | Privacy Policy</span>
    <span class="f-social"><i></i><i></i></span>
  </div>
</footer>

</body>
</html>
```